Market Research firm needs updated business cards with new logo

We need the logo to be included somewhere on the card (attached). We would also like the phrases "Independent, Objective, Comprehensive" and "Research You Can Trust" somewhere on the card. Front or back. Our colors are hex codes 6075a7, e48d25 and 5a5b5b. Though you are certainly not limited to those shades, whatever you produce should coordinate with them. I have also attached our favicon. Feel free to use it in your design, but please do not use it to replace the full logo.

Contact Information for Business Card

see project description

Font styles to use
Other font styles liked:
• Open Sans

Requirements
Must have
• the logo
• We use Open Sans font

```html
<!DOCTYPE html>
<html lang="en">
<head>
<meta charset="utf-8">
<title>Halvern Research – Business Card</title>
<link rel="stylesheet" href="https://fonts.googleapis.com/css2?family=Open+Sans:wght@400;600;700&display=swap">
<style>
  :root {
    --ink: #000000;
    --orange: #e48d25;
    --blue: #6075a7;
    --stage: #9a9a9a;
  }
  * { box-sizing: border-box; margin: 0; padding: 0; }
  html, body {
    width: 1200px;
    height: 1200px;
    overflow: hidden;
    background: var(--stage);
    font-family: "Open Sans", Arial, sans-serif;
  }
  .card {
    position: absolute;
    left: 180px;
    width: 840px;
    height: 480px;
    background: var(--ink);
    overflow: hidden;
  }
  .card--front { top: 82px; }
  .card--back { top: 582px; }

  .brand-name {
    position: absolute;
    color: var(--orange);
    font-weight: 600;
    white-space: nowrap;
    letter-spacing: -0.5px;
  }
  .card--front .brand-name {
    left: 62px;
    top: 44px;
    font-size: 44px;
    line-height: 1;
  }
  .card--back .brand-name {
    left: 0;
    right: 0;
    top: 198px;
    text-align: center;
    font-size: 70px;
    line-height: 1;
    padding-right: 30px;
  }

  .holder {
    position: absolute;
    left: 546px;
    top: 50px;
    color: var(--orange);
  }
  .holder__name {
    font-size: 38px;
    font-weight: 700;
    line-height: 1;
    letter-spacing: 0.5px;
  }
  .holder__role {
    font-size: 28px;
    font-weight: 400;
    line-height: 1;
    margin-left: 10px;
  }

  .contact-band {
    position: absolute;
    left: 0;
    top: 260px;
    width: 840px;
    height: 98px;
    display: flex;
  }
  .contact-band__cell {
    display: flex;
    align-items: center;
    font-size: 21px;
    white-space: nowrap;
  }
  .contact-band__email {
    width: 266px;
    background: var(--orange);
    color: var(--blue);
    padding: 0 0 24px 12px;
    font-size: 20px;
  }
  .contact-band__phone {
    width: 296px;
    background: var(--blue);
    color: var(--orange);
    justify-content: center;
    padding-bottom: 12px;
  }
  .contact-band__web {
    width: 278px;
    background: var(--orange);
    color: var(--blue);
    padding: 6px 0 0 19px;
  }

  .taglines {
    position: absolute;
    top: 418px;
    left: 0;
    width: 840px;
    color: var(--orange);
    font-size: 25px;
    white-space: nowrap;
  }
  .taglines span { position: absolute; top: 0; }
  .taglines .t1 { left: 28px; }
  .taglines .t2 { left: 277px; }
  .taglines .t3 { left: 527px; }
</style>
</head>
<body>
  <section class="card card--front">
    <div class="brand-name">Halvern Research</div>
    <div class="holder">
      <div class="holder__name">JOHN SMITH</div>
      <div class="holder__role">Owner</div>
    </div>
    <div class="contact-band">
      <div class="contact-band__cell contact-band__email">youremail@mailbox.com</div>
      <div class="contact-band__cell contact-band__phone">555 0142 7789</div>
      <div class="contact-band__cell contact-band__web">www.yourwebsite.com</div>
    </div>
    <div class="taglines">
      <span class="t1">Independent</span>
      <span class="t2">Comprehensive</span>
      <span class="t3">Research You Can Trust</span>
    </div>
  </section>

  <section class="card card--back">
    <div class="brand-name">Halvern Research</div>
  </section>
</body>
</html>
```